New Business Card Design Project

We are a spa looking to create a professional elegant business card for a spa mainly black and white with a splash of lime green. This card will be two sided - the front side will have an image, the logo, and the spa's information - the back side will have a promotion for new customers - NEW CUSTOMERS $20 OFF

Look and feel: chic, modern, and spa-ish.
Information to be included:
Therapist Name
Therapist specialty
Address: 4719 Marlowe Ave, Beverly Hills CA 90211
Phone: (310) 482-3917

Let me know if you have any questions!

Thank you

```html
<!DOCTYPE html>
<html lang="en">
<head>
<meta charset="utf-8">
<title>Lumea Day Spa – Business Card</title>
<link rel="stylesheet" href="https://fonts.googleapis.com/css2?family=Arimo:wght@400&family=Questrial&display=swap">
<style>
  :root {
    --backdrop: #8a8a88;
    --card: #e8e8e5;
    --card-tone: #d9d9d4;
    --card-light: #efefec;
    --ink: #1c1c1c;
    --lime: #7dc42a;
    --edge: #f7f7f5;
  }
  * { margin: 0; padding: 0; box-sizing: border-box; }
  html, body { width: 1200px; height: 1200px; overflow: hidden; }
  body {
    background: var(--backdrop);
    font-family: "Arimo", Arial, sans-serif;
    color: var(--ink);
    position: relative;
  }
  .card {
    position: absolute;
    left: 250px;
    width: 700px;
    height: 400px;
    border-radius: 6px;
    overflow: hidden;
    box-shadow: 0 14px 30px rgba(0,0,0,0.28);
    border: 2px solid var(--edge);
  }
  .card--back { top: 120px; }
  .card--front { top: 640px; }
  .card__pattern {
    position: absolute; inset: 0;
    background:
      radial-gradient(circle at 20% 30%, var(--card-light) 0%, transparent 45%),
      radial-gradient(circle at 75% 70%, var(--card-light) 0%, transparent 40%),
      radial-gradient(circle at 55% 20%, var(--card-tone) 0%, transparent 35%),
      linear-gradient(135deg, var(--card) 0%, var(--card-tone) 100%);
  }
  .brand {
    position: absolute;
    left: 44px;
    top: 60px;
    width: 220px;
    height: 190px;
    display: flex;
    align-items: center;
    gap: 16px;
  }
  .brand__dot {
    flex: none;
    width: 40px; height: 40px;
    border-radius: 50%;
    background: var(--ink);
  }
  .brand__name {
    font-family: "Arimo", Arial, sans-serif;
    font-size: 32px;
    line-height: 1.2;
    letter-spacing: 3px;
    text-transform: uppercase;
    color: var(--ink);
  }
  .promo {
    position: absolute;
    left: 300px;
    top: 178px;
    font-size: 28px;
    letter-spacing: 0.5px;
    white-space: nowrap;
  }
  .therapist {
    position: absolute;
    left: 372px;
    top: 178px;
  }
  .therapist__name {
    font-family: "Questrial", sans-serif;
    font-size: 44px;
    letter-spacing: 1px;
    line-height: 1;
  }
  .therapist__role {
    font-size: 30px;
    color: var(--lime);
    margin-left: 48px;
    margin-top: 2px;
  }
  .contact {
    position: absolute;
    display: flex;
    align-items: center;
    gap: 6px;
    font-size: 22px;
    white-space: nowrap;
  }
  .contact--address { left: 34px; bottom: 74px; }
  .contact--phone { right: 40px; bottom: 38px; }
  .contact svg { width: 22px; height: 22px; fill: var(--lime); }
</style>
</head>
<body>

  <section class="card card--back" aria-label="Card back">
    <div class="card__pattern" role="img" aria-label="Soft grey paisley background pattern"></div>
    <div class="brand">
      <span class="brand__dot"></span>
      <span class="brand__name">Lumea<br>Day Spa</span>
    </div>
    <p class="promo">NEW CUSTOMERS $20 OFF</p>
  </section>

  <section class="card card--front" aria-label="Card front">
    <div class="card__pattern" role="img" aria-label="Soft grey paisley background pattern"></div>
    <div class="brand">
      <span class="brand__dot"></span>
      <span class="brand__name">Lumea<br>Day Spa</span>
    </div>
    <div class="therapist">
      <p class="therapist__name">JOHN DOE</p>
      <p class="therapist__role">therapist</p>
    </div>
    <p class="contact contact--address">
      <svg viewBox="0 0 24 24" aria-hidden="true"><path d="M12 3 2 12h3v9h5v-6h4v6h5v-9h3z"/></svg>
      4719 Marlowe Ave, Beverly Hills CA 90211
    </p>
    <p class="contact contact--phone">
      <svg viewBox="0 0 24 24" aria-hidden="true"><path d="M6.6 10.8a15 15 0 0 0 6.6 6.6l2.2-2.2a1 1 0 0 1 1-.25 11.4 11.4 0 0 0 3.6.6 1 1 0 0 1 1 1V20a1 1 0 0 1-1 1A17 17 0 0 1 3 4a1 1 0 0 1 1-1h3.5a1 1 0 0 1 1 1c0 1.250.2 2.45.6 3.6a1 1 0 0 1-.25 1z"/></svg>
      (310) 482-3917
    </p>
  </section>

</body>
</html>
```